Brochure for a new technology in mineral processing industry

We require a rush design for a brochure for an upcoming conference on 8th December. It needs to comply with our logo colours and web site (www.krelvantech.com.au). The attached is a mockup (not very creative) that should be used as a guide only. A word version is available upon request. The design should be aligned with a science and engineering based organisation and not be too busy in its design. Looking for classic but simple lines. Photos loaded up should be used at the designers discretion to enhance look.

Target Market(s)

Brochure to be used to market to mining industry.

Industry/Entity Type

Mining

Requirements
Must have
• The brochure must have simple lines - not to be busy. Colours to match logo and corporate colours and website branding.
Nice to have
• Themes that we feel would be nice to bring through:
• 1. Step Change/modern/innovation
• 2. Clever science being commercialised
• 3. Mining Industry
Should not have
• Not too busy. Arty perspectives.

```html
<!DOCTYPE html>
<html lang="en">
<head>
<meta charset="utf-8">
<title>Glycine Leaching Process – Krelvan Technologies</title>
<link href="https://fonts.googleapis.com/css2?family=Montserrat:wght@400;700;800&family=Poppins:wght@300;400;600&display=swap" rel="stylesheet">
<style>
  :root {
    --brand-blue: #2a6bb8;
    --title-blue: #2f6fb5;
    --ink: #2b2b2b;
    --panel-grey: #e6e7e9;
    --ring-green: #8cc63f;
    --tile-green-1: #a6d99a; --tile-green-2: #6cbb6a;
    --tile-blue-1: #9fd0f2;  --tile-blue-2: #5aa6dc;
    --tile-tan-1: #e6dccb;   --tile-tan-2: #c9b797;
    --tile-grey-1: #eeeeee;  --tile-grey-2: #cdcdcd;
    --tile-yellow-1: #fbf9b6; --tile-yellow-2: #efe969;
    --tile-purple-1: #c5c3ea; --tile-purple-2: #9894d2;
    --tile-border: #8a8a8a;
  }
  * { box-sizing: border-box; margin: 0; padding: 0; }
  html, body { width: 848px; height: 1200px; overflow: hidden; background: #fff; }
  body { position: relative; font-family: "Poppins", Arial, sans-serif; color: var(--ink); }

  .brochure-title {
    position: absolute; left: 43px; top: 62px;
    display: flex; align-items: center; gap: 12px;
    font-weight: 400; font-size: 28px; color: var(--title-blue);
  }
  .title-dot { width: 40px; height: 40px; border-radius: 50%; background: var(--title-blue); }

  .copy { position: absolute; left: 43px; width: 770px; font-size: 16px; line-height: 20.5px; font-weight: 300; }
  .copy p { margin-bottom: 20px; }
  .copy strong { font-weight: 600; }
  .copy-intro { top: 117px; }
  .copy-recovery { top: 818px; }

  .leach-chart { position: absolute; left: 33px; top: 302px; width: 782px; height: 488px; }
  .chart-heading {
    height: 48px; background: var(--brand-blue); color: #fff;
    font-family: "Montserrat", Arial, sans-serif; font-weight: 700; font-size: 14px;
    line-height: 17px; text-align: center; letter-spacing: 0.4px; padding-top: 7px;
  }
  .chart-body { position: relative; height: 372px; background: var(--panel-grey); }
  .chart-footer {
    height: 68px; background: var(--brand-blue);
    display: flex; align-items: center; justify-content: center;
    color: #fff; font-family: "Poppins", Arial, sans-serif; font-weight: 600;
    font-size: 24px; letter-spacing: 2px; text-transform: uppercase;
  }

  .element-grid {
    position: absolute; left: 16px; top: 27px;
    display: grid; grid-template-columns: repeat(10, 67px); grid-auto-rows: 68px;
    column-gap: 8.8px; row-gap: 8px;
  }
  .element {
    border: 1px solid var(--tile-border); border-radius: 7px;
    display: flex; flex-direction: column; align-items: center;
    font-family: "Montserrat", Arial, sans-serif; color: #2a2a2a;
    padding-top: 3px;
  }
  .element .num { font-size: 8px; line-height: 10px; }
  .element .sym { font-size: 27px; font-weight: 800; line-height: 30px; letter-spacing: -0.5px; }
  .element .name, .element .mass { font-size: 8px; line-height: 9px; }
  .col-2 { grid-column-start: 2; }

  .green  { background: linear-gradient(160deg, var(--tile-green-1), var(--tile-green-2)); }
  .blue   { background: linear-gradient(160deg, var(--tile-blue-1), var(--tile-blue-2)); }
  .tan    { background: linear-gradient(160deg, var(--tile-tan-1), var(--tile-tan-2)); }
  .grey   { background: linear-gradient(160deg, var(--tile-grey-1), var(--tile-grey-2)); }
  .yellow { background: linear-gradient(160deg, var(--tile-yellow-1), var(--tile-yellow-2)); }
  .purple { background: linear-gradient(160deg, var(--tile-purple-1), var(--tile-purple-2)); }

  .legend {
    position: absolute; left: 16px; top: 275px;
    display: grid; grid-template-columns: repeat(6, 109px); column-gap: 18.6px;
  }
  .legend-key {
    height: 79px; border: 1px solid var(--tile-border); border-radius: 7px;
    display: flex; align-items: center; justify-content: center; text-align: center;
    font-family: "Montserrat", Arial, sans-serif; font-weight: 700; font-size: 10px; line-height: 12px;
    padding: 0 6px;
  }

  .photo-row { position: absolute; top: 993px; left: 73px; display: flex; gap: 125px; }
  .photo {
    width: 148px; height: 148px; border-radius: 50%;
    border: 4px solid var(--ring-green); padding: 6px; background: #fff;
  }
  .photo span { display: block; width: 100%; height: 100%; border-radius: 50%; }
  .photo-metal span { background: radial-gradient(circle at 40% 45%, #d9d9d9, #8a8a8a 55%, #3c3c3c); }
  .photo-ore-green span { background: radial-gradient(circle at 45% 45%, #c49a3a, #3f6f6c 50%, #1e2f4a); }
  .photo-ore-blue span { background: radial-gradient(circle at 50% 50%, #6a5a9a, #2e3f78 55%, #7a3a4a); }
</style>
</head>
<body>
  <h1 class="brochure-title"><span class="title-dot"></span>Glycine Leaching Process</h1>

  <section class="copy copy-intro">
    <p>The Glycine Leaching Process is an environmentally benign hydrometallurgical process that will leach base and precious metal oxide, mixed oxide and sulphide ores.</p>
    <p>Glycine is the simplest and cheapest amino acid, and is available in bulk in different grades. <strong>It is an environmentally safe and stable reagent</strong> and is biodegradable and easily metabolized in most living organisms.</p>
    <p><strong>It is selective on which metals it leaches and does not leach common gangue minerals.</strong></p>
  </section>

  <section class="leach-chart">
    <h2 class="chart-heading">Leaching characteristics of metals under consideration at<br>pH values between 9 and 12 with Sodium Glycinate as solvent</h2>
    <div class="chart-body">
      <div class="element-grid">
        <div class="element blue"><span class="num">25</span><span class="sym">Mn</span><span class="name">Manganese</span><span class="mass">54.9</span></div>
        <div class="element blue"><span class="num">26</span><span class="sym">Fe</span><span class="name">Iron</span><span class="mass">55.9</span></div>
        <div class="element tan"><span class="num">27</span><span class="sym">Co</span><span class="name">Colbalt</span><span class="mass">58.9</span></div>
        <div class="element tan"><span class="num">28</span><span class="sym">Ni</span><span class="name">Nickel</span><span class="mass">58.7</span></div>
        <div class="element tan"><span class="num">29</span><span class="sym">Cu</span><span class="name">Copper</span><span class="mass">63.5</span></div>
        <div class="element grey"><span class="num">30</span><span class="sym">Zn</span><span class="name">Zinc</span><span class="mass">65.4</span></div>
        <div class="element green"><span class="num">31</span><span class="sym">Ga</span><span class="name">Gallium</span><span class="mass">69.7</span></div>
        <div class="element green"><span class="num">32</span><span class="sym">Ge</span><span class="name">Germanium</span><span class="mass">72.6</span></div>
        <div class="element purple"><span class="num">33</span><span class="sym">As</span><span class="name">Arsenic</span><span class="mass">74.9</span></div>
        <div class="element purple"><span class="num">34</span><span class="sym">Se</span><span class="name">Selenium</span><span class="mass">79.0</span></div>

        <div class="element green col-2"><span class="num">44</span><span class="sym">Ru</span><span class="name">Ruthenium</span><span class="mass">101.0</span></div>
        <div class="element green"><span class="num">45</span><span class="sym">Rh</span><span class="name">Rhodium</span><span class="mass">102.9</span></div>
        <div class="element yellow"><span class="num">46</span><span class="sym">Pd</span><span class="name">Palladium</span><span class="mass">106.4</span></div>
        <div class="element tan"><span class="num">47</span><span class="sym">Ag</span><span class="name">Silver</span><span class="mass">107.9</span></div>
        <div class="element grey"><span class="num">48</span><span class="sym">Cd</span><span class="name">Cadmium</span><span class="mass">112.4</span></div>
        <div class="element green"><span class="num">49</span><span class="sym">In</span><span class="name">Indium</span><span class="mass">114.8</span></div>
        <div class="element green"><span class="num">50</span><span class="sym">Sn</span><span class="name">Tin</span><span class="mass">118.7</span></div>
        <div class="element purple"><span class="num">51</span><span class="sym">Sb</span><span class="name">Antimony</span><span class="mass">121.8</span></div>
        <div class="element purple"><span class="num">52</span><span class="sym">Te</span><span class="name">Tellurium</span><span class="mass">127.6</span></div>

        <div class="element green col-2"><span class="num">76</span><span class="sym">Os</span><span class="name">Osmium</span><span class="mass">190.2</span></div>
        <div class="element green"><span class="num">77</span><span class="sym">Ir</span><span class="name">Iridium</span><span class="mass">192.2</span></div>
        <div class="element yellow"><span class="num">78</span><span class="sym">Pt</span><span class="name">Platinum</span><span class="mass">195.1</span></div>
        <div class="element tan"><span class="num">79</span><span class="sym">Au</span><span class="name">Gold</span><span class="mass">197.0</span></div>
        <div class="element green"><span class="num">80</span><span class="sym">Hg</span><span class="name">Mercury</span><span class="mass">200.6</span></div>
        <div class="element green"><span class="num">81</span><span class="sym">Tl</span><span class="name">Thallium</span><span class="mass">204.4</span></div>
        <div class="element grey"><span class="num">82</span><span class="sym">Pb</span><span class="name">Lead</span><span class="mass">207.2</span></div>
        <div class="element purple"><span class="num">83</span><span class="sym">Bi</span><span class="name">Bismuth</span><span class="mass">209.0</span></div>
      </div>

      <div class="legend">
        <div class="legend-key green">Glycine Solubility Unknown</div>
        <div class="legend-key blue">Known Clycine Insoluble</div>
        <div class="legend-key tan">Known Glycine Leachable</div>
        <div class="legend-key grey">Known Glycine Leachable Limited Test work</div>
        <div class="legend-key yellow">Unknown Subject to Experiment</div>
        <div class="legend-key purple">Known Amphoteric Anions</div>
      </div>
    </div>
    <div class="chart-footer">Krelvan Technologies</div>
  </section>

  <section class="copy copy-recovery">
    <p><strong>It is easily recovered and recycled.</strong> Flow sheet test work and modelling to date has shown that less than 5% Glycine loss can be expected. This means low reagent consumption costs for the major leaching reagent.</p>
    <p>It is a simple process than can be used with “off the shelf” items of equipment.</p>
    <p>Several applications of the technology are being developed.</p>
  </section>

  <div class="photo-row">
    <div class="photo photo-metal"><span role="img" aria-label="Photo of a piece of raw silver-grey metal"></span></div>
    <div class="photo photo-ore-green"><span role="img" aria-label="Close-up photo of mineral ore with green nodules"></span></div>
    <div class="photo photo-ore-blue"><span role="img" aria-label="Close-up photo of blue and purple mineral ore"></span></div>
  </div>
</body>
</html>
```